Website for Life Strategies business

We need a website to present our video, audio and print content to subcribers at Bright Summit Mentors. We will offer a team of coaches who can help people breakthrough the barriers that keep them from reaching their physical, spiritual, financial, leadership and relationship goals.

Target Market(s)

Anyone who needs help with strategies to take their life to a new level of success.

Industry/Entity Type

Life Coaching

Logo Text

Bright Summit Mentors

Number of Pages Required

5+ page

Colors

Designer to choose colors to be used in the design.

Requirements
Must have
• The ability to present content as a package that includes Word Documents, videos and audio content as well as to be able to display books for sale. Each week their would be a new package for subscribers to access. It should provide the ability for subscribers to comment on the material and share how their lives were changed by the content. Should also include a shop page to offer merchandise for sale.
Nice to have
• Not sure
Should not have
• Not sure

```html
<!DOCTYPE html>
<html lang="en">
<head>
<meta charset="utf-8">
<title>Bright Summit Mentors</title>
<link href="https://fonts.googleapis.com/css2?family=Montserrat:wght@400;500;600;700&display=swap" rel="stylesheet">
<style>
:root{
  --brand:#1a5fd0;
  --brand-dark:#1350b8;
  --ink:#2b2b2b;
  --muted:#6b6b6b;
  --white:#ffffff;
  --footer:#3a3a3a;
  --footer-text:#bdbdbd;
  --line:#e4e4e4;
}
*{margin:0;padding:0;box-sizing:border-box}
html,body{width:1200px;height:2941px;overflow:hidden}
body{font-family:"Montserrat",Arial,sans-serif;color:var(--ink);background:var(--white);position:relative}
.abs{position:absolute}
.center{left:0;width:1200px;text-align:center}

/* header */
.site-header{top:0;left:0;width:1200px;height:88px;background:var(--white)}
.logo{left:130px;top:22px;font-size:32px;font-weight:500;color:var(--brand);letter-spacing:.2px}
.main-nav{right:132px;top:38px;display:flex;gap:24px;font-size:11px;font-weight:500;color:#555;text-transform:uppercase}
.main-nav .active{color:var(--brand);border-bottom:1px solid var(--brand)}

/* hero */
.hero{top:88px;left:0;width:1200px;height:526px;background:linear-gradient(180deg,#d9dde6 0%,#c7c8dc 25%,#b9c3d3 50%,#8c98ab 75%,#6f6a63 100%)}
.hero-title{top:190px;font-size:41px;font-weight:700;color:#1f1f1f;letter-spacing:1px}
.hero-sub{top:238px;font-size:31px;font-weight:500;color:#1f1f1f}
.btn-outline{left:547px;top:288px;width:106px;height:38px;border:2px solid #222;font-size:11px;font-weight:600;line-height:34px;text-align:center;color:#222;background:rgba(255,255,255,.25)}
.slider-arrow{top:250px;width:30px;height:30px;border-radius:50%;background:rgba(255,255,255,.45)}
.slider-arrow svg{display:block;margin:8px auto}

/* intro */
.intro-text{top:688px;font-size:19px;line-height:28px;color:var(--muted)}
.intro-text strong{color:var(--ink);font-weight:500}
.btn-solid{left:500px;top:752px;width:200px;height:49px;background:var(--brand);color:var(--white);font-size:15px;font-weight:500;line-height:49px;text-align:center}

/* what we do */
.services{top:882px;left:0;width:1200px;height:523px;background:linear-gradient(180deg,#8a7ee0 0%,#5f79e8 35%,#4f6fe6 65%,#6d5ec9 100%)}
.section-title-light{top:70px;font-size:29px;font-weight:400;color:var(--white)}
.service-card{top:135px;width:298px}
.service-photo{height:200px}
.service-caption{margin-top:13px;text-align:center;color:var(--white);font-size:17px}

/* media */
.media-title{top:1476px;font-size:30px;font-weight:500;color:var(--brand)}
.media-arrow{top:1484px;width:24px;height:24px;border:1px solid #aaa;background:var(--white)}
.media-arrow svg{display:block;margin:6px auto}
.media-tile{overflow:hidden}
.media-badge{position:absolute;left:0;top:0;width:32px;height:32px;background:var(--brand)}
.media-badge svg{display:block;margin:9px auto}
.play{position:absolute;left:50%;top:50%;width:44px;height:44px;margin:-22px 0 0 -22px;border-radius:50%;background:var(--white)}
.play svg{display:block;margin:13px 0 0 16px}
.media-text-card{background:#262626;color:var(--white);text-align:center;padding:40px 18px 0}
.media-text-card h3{font-size:17px;font-weight:500;line-height:26px;margin-bottom:14px}
.media-text-card p{font-size:10px;line-height:17px;color:#ddd}
.view-all{left:451px;width:297px;top:2218px;text-align:center;font-size:17px;color:#444}

/* success stories */
.stories{top:2320px;left:0;width:1200px;height:422px;background:linear-gradient(180deg,#dce6f0 0%,#cfdcea 45%,#b7c7d7 75%,#9aa7b0 100%)}
.stories-figure{left:0;top:60px;width:260px;height:362px;background:linear-gradient(180deg,#d9b79a 0%,#1fa5a8 40%,#1a8d92 75%,#b29d86 100%);opacity:.85}
.stories-title{top:62px;font-size:30px;font-weight:500;color:var(--brand)}
.quote{top:118px;left:300px;width:600px;text-align:center;font-size:17.5px;line-height:26px;color:#222}
.quote-name{top:210px;font-size:12px;color:#333}
.avatar{left:561px;top:237px;width:78px;height:78px;border-radius:50%;background:#9aa3ab;border:3px solid var(--white)}
.dots{top:340px;display:flex;justify-content:center;gap:16px}
.dots span{width:7px;height:7px;border-radius:50%;background:#6c7b8c}
.dots span.on{background:var(--brand)}

/* contact bar */
.contact-bar{top:2742px;left:0;width:1200px;height:85px;background:var(--white)}
.contact-item{top:33px;font-size:15px;color:#444;display:flex;align-items:center;gap:6px}

/* footer */
.site-footer{top:2827px;left:0;width:1200px;height:114px;background:var(--footer)}
.footer-links{left:130px;top:36px;font-size:10px;color:var(--footer-text)}
.footer-links span{margin:0 6px}
.copyright{left:130px;top:62px;font-size:10px;color:var(--footer-text)}
.social{right:134px;top:42px;display:flex;gap:8px}
.social i{display:block;width:22px;height:22px;border-radius:50%;background:#8d8d8d}
</style>
</head>
<body>

<header class="site-header abs">
  <div class="logo abs">Bright Summit Mentors</div>
  <nav class="main-nav abs">
    <span class="active">Home</span><span>About</span><span>Services</span><span>Media</span><span>Success Stories</span><span>Contact</span>
  </nav>
</header>

<section class="hero abs" role="img" aria-label="Photo of a hiker standing on a rocky ledge above a glacier valley">
  <div class="hero-title abs center">INTEGER DAPIBUS</div>
  <div class="hero-sub abs center">augue at accumsan volutpat</div>
  <div class="btn-outline abs">READ MORE</div>
  <div class="slider-arrow abs" style="left:22px"><svg width="10" height="14" viewBox="0 0 10 14"><path d="M8 1 2 7l6 6" fill="none" stroke="#fff" stroke-width="2.5"/></svg></div>
  <div class="slider-arrow abs" style="right:22px"><svg width="10" height="14" viewBox="0 0 10 14"><path d="M2 1l6 6-6 6" fill="none" stroke="#fff" stroke-width="2.5"/></svg></div>
</section>

<section class="intro">
  <p class="intro-text abs center">We will offer a team of coaches who can help people breakthrough the barriers that keep them<br>from reaching their <strong>physical, spiritual, financial, leadership and relationship goals.</strong></p>
  <div class="btn-solid abs">GET STARTED NOW</div>
</section>

<section class="services abs" role="img" aria-label="Blue and violet sky over sea with a silhouette of a runner">
  <h2 class="section-title-light abs center">WHAT WE DO</h2>
  <div class="service-card abs" style="left:131px">
    <div class="service-photo" style="background:linear-gradient(135deg,#e9e6e1,#c9c3ba)" role="img" aria-label="Photo of a counselling session on a sofa"></div>
    <div class="service-caption">Curabitur feugiat sed</div>
  </div>
  <div class="service-card abs" style="left:451px">
    <div class="service-photo" style="background:linear-gradient(135deg,#8a8580,#c7a789)" role="img" aria-label="Photo of a trainer coaching a man lifting dumbbells"></div>
    <div class="service-caption">Quisque vel venenatis</div>
  </div>
  <div class="service-card abs" style="left:769px">
    <div class="service-photo" style="background:linear-gradient(135deg,#eef0f1,#9ea4a8)" role="img" aria-label="Photo of a speaker presenting to a seated group"></div>
    <div class="service-caption">Aliquam vitae porta</div>
  </div>
</section>

<section class="media">
  <div class="media-arrow abs" style="left:130px"><svg width="6" height="10" viewBox="0 0 6 10"><path d="M5 1 1 5l4 4" fill="none" stroke="#777" stroke-width="1.3"/></svg></div>
  <h2 class="media-title abs center">MEDIA</h2>
  <div class="media-arrow abs" style="left:1042px"><svg width="6" height="10" viewBox="0 0 6 10"><path d="M1 1l4 4-4 4" fill="none" stroke="#777" stroke-width="1.3"/></svg></div>

  <div class="media-tile abs" style="left:131px;top:1537px;width:297px;height:377px;background:linear-gradient(160deg,#e4e2df,#a88a74)" role="img" aria-label="Photo of a smiling woman in a knit sweater">
    <div class="media-badge"><svg width="12" height="14" viewBox="0 0 12 14"><path d="M1 1h7l3 3v9H1z" fill="none" stroke="#fff" stroke-width="1.4"/><path d="M3 7h6M3 10h6" stroke="#fff" stroke-width="1.2"/></svg></div>
  </div>
  <div class="media-tile abs" style="left:451px;top:1537px;width:297px;height:297px;background:linear-gradient(160deg,#5a6a5c,#b58a66)" role="img" aria-label="Video still of a laughing couple at a cafe table">
    <div class="media-badge"><svg width="14" height="10" viewBox="0 0 14 10"><rect x="0" y="1" width="9" height="8" fill="#fff"/><path d="M9 5l5-4v8z" fill="#fff"/></svg></div>
    <div class="play"><svg width="14" height="18" viewBox="0 0 14 18"><path d="M0 0l14 9-14 9z" fill="#333"/></svg></div>
  </div>
  <div class="media-tile abs" style="left:770px;top:1537px;width:297px;height:377px;background:linear-gradient(180deg,#e4f1f8,#8fb9d6 55%,#4d6d8e)" role="img" aria-label="Photo of a man climbing a long staircase toward bright sky">
    <div class="media-badge"><svg width="12" height="14" viewBox="0 0 12 14"><path d="M1 1h7l3 3v9H1z" fill="none" stroke="#fff" stroke-width="1.4"/><path d="M3 7h6M3 10h6" stroke="#fff" stroke-width="1.2"/></svg></div>
  </div>

  <div class="media-tile abs" style="left:131px;top:1940px;width:297px;height:297px;background:linear-gradient(160deg,#d7dde0,#c2737f)" role="img" aria-label="Video still of a woman with a water bottle after a workout">
    <div class="media-badge"><svg width="14" height="12" viewBox="0 0 14 12"><path d="M1 4h3l4-3v10L4 8H1z" fill="#fff"/><path d="M10 3q2 3 0 6" fill="none" stroke="#fff" stroke-width="1.3"/></svg></div>
    <div class="play"><svg width="14" height="18" viewBox="0 0 14 18"><path d="M0 0l14 9-14 9z" fill="#333"/></svg></div>
  </div>
  <div class="media-tile media-text-card abs" style="left:451px;top:1858px;width:297px;height:298px">
    <div class="media-badge"><svg width="14" height="14" viewBox="0 0 14 14"><rect x="1" y="4" width="8" height="9" fill="none" stroke="#fff" stroke-width="1.4"/><path d="M5 4V1h8v9h-4" fill="none" stroke="#fff" stroke-width="1.4"/></svg></div>
    <h3>Pellentesque iaculis condi mentum quam, eu pulvinar quam</h3>
    <p>Nullam vitae imperdiet nisl. Phasellus maximus elit dolor, vitae fringilla justo consequat sed. Donec a eleifend enim. Mauris ac felis elit. Donec ut leo et dui fermentum venenatis. Sed eget nulla consequat, suscipit purus pharetra, facilisis est. Maecenas in fringilla nisl. Pellentesque faucibus mi a nulla efficitur.</p>
  </div>
  <div class="media-tile abs" style="left:770px;top:1940px;width:297px;height:297px;background:linear-gradient(160deg,#f1f1ef,#7a8797)" role="img" aria-label="Photo of two colleagues reviewing work at a laptop">
    <div class="media-badge"><svg width="14" height="14" viewBox="0 0 14 14"><rect x="1" y="4" width="8" height="9" fill="none" stroke="#fff" stroke-width="1.4"/><path d="M5 4V1h8v9h-4" fill="none" stroke="#fff" stroke-width="1.4"/></svg></div>
  </div>
  <div class="view-all abs">View All</div>
</section>

<section class="stories abs" role="img" aria-label="Mountain landscape under a pale sky">
  <div class="stories-figure abs" role="img" aria-label="Photo of a woman resting on rocks overlooking the view"></div>
  <h2 class="stories-title abs center">SUCCESS STORIES</h2>
  <p class="quote abs">“ Mauris non commodo metus. Donec lacinia et dolor non aliquet. Aenean vel diam nunc. Phasellus vestibulum nisi venenatis urna blandit, eget porttitor ligula elementum. ”</p>
  <div class="quote-name abs center">- Evan Marsh, City</div>
  <div class="avatar abs" role="img" aria-label="Portrait of the client"></div>
  <div class="dots abs center"><span class="on"></span><span></span><span></span><span></span></div>
</section>

<section class="contact-bar abs">
  <div class="contact-item abs" style="left:130px"><svg width="10" height="14" viewBox="0 0 10 14"><path d="M5 0a5 5 0 0 1 5 5c0 4-5 9-5 9S0 9 0 5a5 5 0 0 1 5-5z" fill="#444"/><circle cx="5" cy="5" r="2" fill="#fff"/></svg>24 Building name, Street name, City - Zipcode</div>
  <div class="contact-item abs" style="left:585px"><svg width="9" height="14" viewBox="0 0 9 14"><rect x="1" y="1" width="7" height="12" rx="1" fill="none" stroke="#444" stroke-width="1.3"/></svg>555 013 4827</div>
  <div class="contact-item abs" style="left:789px"><svg width="14" height="11" viewBox="0 0 14 11"><rect x="0" y="0" width="14" height="11" fill="#444"/><path d="M0 0l7 6 7-6" fill="none" stroke="#fff" stroke-width="1.2"/></svg>info@brightsummitmentors.com</div>
</section>

<footer class="site-footer abs">
  <div class="footer-links abs">Home<span>|</span>About<span>|</span>Services<span>|</span>Media<span>|</span>Success Stories<span>|</span>Contact</div>
  <div class="copyright abs">Copyright © 2017 Bright Summit Mentors. All rights reserved.</div>
  <div class="social abs"><i></i><i></i><i></i><i></i><i></i><i></i><i></i><i></i><i></i></div>
</footer>

</body>
</html>
```